Australian Trucking Company Requires Professional Looking Stationary

We require a professional looking stationary design that incorporates our newly designed logo.

Our business, called "Brell Haulage Contracting", provides contracting work, transport and logistics to business in Western Australia particularly with links to the mining sector.

We are a small business looking to expand and our new logo and our new stationary will help develop our brand image in our market place.

Target Market(s)

Businesses and Corporation with links to the Mining Sector

Industry/Entity Type

Small Business

Requirements
Must have
• The letterhead must have the following details:
The new logo

Text saying: "Brell Holdings Pty Ltd (ACN 582 316 907) ATF The Brell Discretionary Trust T/AS"
"ABN 71 834 209 553"
Address "P.O Box 817 Wattlegrove WA, 6958"
Phone: 08 9352 7140
Email: brellhaul@mailbox-example.com.au

The text on the letterhead should be editable as the details are likely to change in the near future. Provision should be made for a website address all though one isn't available at the moment.

The styling, layout and font text is entirely up to the designer.

```html
<!DOCTYPE html>
<html lang="en">
<head>
<meta charset="utf-8">
<title>Brell Haulage Contracting – Business Card</title>
<link rel="stylesheet" href="https://fonts.googleapis.com/css2?family=Arimo:wght@400;700&display=swap">
<style>
  :root {
    --bg: #e9e6e2;
    --card-white: #ffffff;
    --brand-red: #8f161c;
    --bright-red: #b81e25;
    --grey-light: #d4d4d4;
    --grey-dark: #7c7c7c;
    --text-light: #ffffff;
  }
  * { margin: 0; padding: 0; box-sizing: border-box; }
  html, body {
    width: 1200px; height: 665px; overflow: hidden;
    background: var(--bg);
    font-family: "Arimo", Arial, sans-serif;
  }
  .canvas { position: relative; width: 1200px; height: 665px; }

  .card {
    position: absolute; top: 168px;
    width: 520px; height: 330px;
    border-radius: 24px; overflow: hidden;
    box-shadow: 0 6px 18px rgba(0,0,0,.18);
  }
  .card--front { left: 50px; background: var(--card-white); }
  .card--back { left: 630px; background: var(--brand-red); }

  .card__shapes { position: absolute; inset: 0; }

  .brand {
    position: absolute; left: 34px; top: 48px;
    display: flex; align-items: center; gap: 14px;
  }
  .brand__mark {
    width: 54px; height: 54px; border-radius: 50%;
    background: var(--grey-dark);
  }
  .brand__name {
    color: var(--brand-red);
    font-weight: 700; font-size: 23px; line-height: 1.02;
    text-transform: uppercase; letter-spacing: .5px;
  }

  .contact {
    position: absolute; right: 20px; top: 110px;
    text-align: right; color: var(--text-light);
  }
  .contact__name { font-weight: 700; font-size: 17px; }
  .contact__title { font-size: 12px; margin: 4px 0 24px; }
  .contact__line {
    display: flex; justify-content: flex-end; align-items: center; gap: 6px;
    font-size: 11px; margin-bottom: 8px;
  }
  .contact__line svg { width: 11px; height: 11px; flex: none; }
  .contact__address { font-size: 11px; margin-top: 12px; }

  .abn {
    position: absolute; left: 142px; bottom: 30px;
    color: var(--text-light); font-size: 11px;
  }

  .back__decor {
    position: absolute; left: 200px; top: 40px;
    width: 210px; height: 210px; border-radius: 50%;
    background: radial-gradient(circle, rgba(255,255,255,.22), rgba(255,255,255,.05));
  }
  .back__legal {
    position: absolute; left: 0; right: 0; bottom: 34px;
    text-align: center; color: var(--text-light); font-size: 11px;
  }
</style>
</head>
<body>
<main class="canvas">

  <section class="card card--front" aria-label="Business card front">
    <svg class="card__shapes" viewBox="0 0 520 330" aria-hidden="true">
      <defs>
        <linearGradient id="grey-sweep" x1="0" y1="0" x2="1" y2="1">
          <stop offset="0" stop-color="#d4d4d4"/>
          <stop offset="1" stop-color="#7c7c7c"/>
        </linearGradient>
      </defs>
      <path d="M50 330 C55 292 88 272 114 272 C109 292 107 312 109 330 Z" fill="#b81e25"/>
      <path d="M120 330 C136 225 198 158 268 146 C258 205 254 280 262 330 Z" fill="url(#grey-sweep)"/>
      <path d="M275 330 C270 240 278 165 312 128 C352 92 450 92 520 86 L520 330 Z" fill="#8f161c"/>
    </svg>

    <div class="brand">
      <span class="brand__mark" aria-hidden="true"></span>
      <div class="brand__name">Brell<br>Haulage<br>Contracting</div>
    </div>

    <div class="contact">
      <div class="contact__name">Name here</div>
      <div class="contact__title">Title</div>
      <div class="contact__line">08 9352 7140
        <svg viewBox="0 0 12 12" aria-hidden="true"><circle cx="6" cy="6" r="5.2" fill="none" stroke="#fff"/><path d="M4 3.5 Q3.5 7 7.5 8.5" fill="none" stroke="#fff" stroke-width="1.4"/></svg>
      </div>
      <div class="contact__line">brellhaul@mailbox-example.com.au
        <svg viewBox="0 0 12 12" aria-hidden="true"><rect x="1" y="2.5" width="10" height="7" fill="#fff"/><path d="M1 2.5 L6 6.5 L11 2.5" fill="none" stroke="#8f161c"/></svg>
      </div>
      <div class="contact__line">www.brellhaulage-example.com
        <svg viewBox="0 0 12 12" aria-hidden="true"><circle cx="6" cy="6" r="5" fill="none" stroke="#fff"/><ellipse cx="6" cy="6" rx="2.2" ry="5" fill="none" stroke="#fff"/><path d="M1 6 H11" stroke="#fff"/></svg>
      </div>
      <div class="contact__address">P.O Box 817 Wattlegrove WA, 6958</div>
    </div>

    <div class="abn">ABN 71 834 209 553</div>
  </section>

  <section class="card card--back" aria-label="Business card back">
    <div class="back__decor" aria-hidden="true"></div>
    <p class="back__legal">Brell Holdings Pty Ltd (ACN 582 316 907) ATF The Brell Discretionary Trust T/AS</p>
  </section>

</main>
</body>
</html>
```